English and Spanish Language School Needs a Business Card

Need a business card design a startup company called Maribel Language School. The company will offer English and Spanish conversational level courses designed to make the learner feel comfortable with grammar and vocabulary. We would like to see a logo with some colour that should communicate learning, growth.

Target Market(s)

Consumers and businesses

Industry/Entity Type

Education

Contact Information for Business Card

TBD

Font styles to use
Serif

Requirements
Must have
• Include the following
• Logo
• Name
• Title
• Cellphone Number
• Office Phone number
• Email address
• Office Address

```html
<!DOCTYPE html>
<html lang="en">
<head>
<meta charset="utf-8">
<title>Maribel Language School – Business Card</title>
<link rel="stylesheet" href="https://fonts.googleapis.com/css2?family=Montserrat:wght@400;600;700&display=swap">
<style>
  :root {
    --bg: #ecebe8;
    --card-white: #ffffff;
    --brand-red: #c91d2b;
    --brand-red-light: #df3d4a;
    --ink-dark: #2b2b2b;
    --teal: #1fa3a8;
    --shadow: rgba(0, 0, 0, 0.18);
  }
  * { box-sizing: border-box; margin: 0; padding: 0; }
  html, body { width: 1200px; height: 913px; overflow: hidden; }
  body {
    background: var(--bg);
    font-family: "Montserrat", sans-serif;
    position: relative;
  }
  .card {
    position: absolute;
    width: 540px;
    height: 309px;
    border-radius: 16px;
    overflow: hidden;
    box-shadow: 0 10px 28px var(--shadow);
  }

  /* Front side */
  .card-front { left: 70px; top: 130px; background: var(--card-white); }
  .front-band {
    position: absolute;
    left: 0; top: 130px;
    width: 300px; height: 135px;
    background: linear-gradient(180deg, var(--brand-red-light), var(--brand-red));
  }
  .front-logo {
    position: absolute;
    left: 28px; top: 170px;
    color: var(--ink-dark);
    font-weight: 700;
    line-height: 1;
  }
  .logo-name { display: block; font-size: 50px; letter-spacing: -1px; }
  .logo-sub { display: block; font-size: 15px; margin-top: 4px; font-weight: 700; }

  .accent-bar {
    position: absolute;
    left: 300px; top: 108px;
    width: 10px; height: 22px;
    background: var(--ink-dark);
  }
  .contact {
    position: absolute;
    left: 318px; top: 92px;
    color: var(--teal);
    font-size: 12px;
    line-height: 1.45;
  }
  .contact-name { color: var(--brand-red); font-size: 19px; font-weight: 600; line-height: 1.1; }
  .contact-title { margin-bottom: 10px; }
  .contact-address { margin-bottom: 8px; }
  .contact-row { display: flex; align-items: center; gap: 8px; }
  .contact-row svg { width: 10px; height: 10px; flex: none; }
  .contact-web { color: var(--brand-red); font-weight: 700; }

  /* Back side */
  .card-back {
    left: 590px; top: 470px;
    background: linear-gradient(160deg, var(--brand-red-light), var(--brand-red) 60%);
    color: var(--card-white);
  }
  .back-logo {
    position: absolute;
    left: 0; right: 0; top: 88px;
    text-align: center;
    font-weight: 700;
    line-height: 1;
  }
  .back-logo .logo-name { font-size: 66px; }
  .back-logo .logo-sub { font-size: 18px; margin-top: 6px; }
  .back-web {
    position: absolute;
    left: 0; right: 0; bottom: 42px;
    text-align: center;
    font-size: 12px;
    font-weight: 600;
    letter-spacing: 0.3px;
  }
</style>
</head>
<body>

  <section class="card card-front" aria-label="Business card front">
    <div class="front-band"></div>
    <div class="front-logo">
      <span class="logo-name">Maribel</span>
      <span class="logo-sub">Language School</span>
    </div>
    <div class="accent-bar"></div>
    <div class="contact">
      <p class="contact-name">Lena Hartwell</p>
      <p class="contact-title">Director</p>
      <p class="contact-address">Po Box 218<br>Ashford VIC 3902</p>
      <p class="contact-row">
        <svg viewBox="0 0 10 10"><rect x="2.5" y="0.5" width="5" height="9" rx="1" fill="none" stroke="#c91d2b" stroke-width="1"/></svg>
        +330 2418-5093
      </p>
      <p class="contact-row">
        <svg viewBox="0 0 10 10"><path d="M2 1 L4 1 L5 3.5 L3.8 4.5 Q5 6.5 6 6.6 L7 5.5 L9 6.5 L9 8.5 Q4 9.5 1 2.5 Z" fill="#c91d2b"/></svg>
        +330 2471-6628
      </p>
      <p class="contact-row">
        <svg viewBox="0 0 10 10"><rect x="0.5" y="2" width="9" height="6" fill="none" stroke="#c91d2b" stroke-width="1"/><path d="M0.5 2 L5 5.5 L9.5 2" fill="none" stroke="#c91d2b" stroke-width="1"/></svg>
        hello@maribelschool.com
      </p>
      <p class="contact-row contact-web">
        <svg viewBox="0 0 10 10"><circle cx="5" cy="5" r="4.5" fill="#c91d2b"/><path d="M0.5 5 H9.5 M5 0.5 V9.5" stroke="#fff" stroke-width="0.8"/></svg>
        maribellanguageschool.com
      </p>
    </div>
  </section>

  <section class="card card-back" aria-label="Business card back">
    <div class="back-logo">
      <span class="logo-name">Maribel</span>
      <span class="logo-sub">Language School</span>
    </div>
    <p class="back-web">www.maribellanguageschool.com</p>
  </section>

</body>
</html>
```